Website for research group at university relating to human wildlife conflict

Australian university based research group. Researching the relationship between humans and wildlife, and seeking to explore ways for the two to coexist. The research group is called "Creature Harmony NexaForm lab" (NexaForm=coexistence, which should be spelled out somewhere)

I have a logo for the research group (from artflockly). it is attached. I like it when the logo can be used throughout the website (e.g for titles, and in backgrounds).

Just a simple and clean/modern feel. i like the following websites as examples, but also like to be a little different!
https://www.feralvantis.org/
http://www.qmbrn.org/

At least one large image on each page, like a banner (just put in one and i can replace them). Images of Australian wildlife preferred (especially canids), and images with humans and animals helps too.

I would like the following pages
Home page (including Vision statement; and link to twitter account).
THEN, the following pages- which can all be the same/similar design with minor differences according to content of that page.
People (inc photo and profile)
Publications (list of publications by topic)
Projects (details of projects- with title, photo, detail)
News items (by topic, with title, image, link)
Contact
Collaborators (list of groups and people we associated with group- name and photo)

Target Market(s)

government. researchers. university.

Industry/Entity Type

University

Coding

Coded - Design and coding required

Number of Pages Required

5+ page

Font styles to use
Sans Serif

Colors

Designer to choose colors to be used in the design.

Requirements
Must have
• I require all the coded files so that i have flexibility of where i can host it.
• must have my logo.
• must have a visually appealing, modern and easy to navigate landing page.
• must have a large photo (e.g banner) at the top of every page.
• must have twitter feed on home page.
Nice to have
• I require all the coded files so that i have the flexibility of where i can host it.

```html
<!DOCTYPE html>
<html lang="en">
<head>
<meta charset="utf-8">
<title>Creature Harmony NexaForm lab</title>
<link href="https://fonts.googleapis.com/css2?family=Montserrat:wght@400;500;600;700&display=swap" rel="stylesheet">
<style>
:root{
  --orange:#e8642c;
  --green:#4b7a1f;
  --green-dark:#4a6b22;
  --ink:#333;
  --muted:#555;
  --grey-bg:#ebebeb;
  --white:#fff;
  --sky:#1aa5e8;
  --footer:#2b2b2b;
}
*{box-sizing:border-box;margin:0;padding:0}
html,body{width:1200px;height:3340px;overflow:hidden}
body{font-family:'Montserrat',sans-serif;color:var(--ink);background:var(--white);position:relative}
section,header,footer{position:relative;width:1200px}
.abs{position:absolute}
.btn{position:absolute;background:var(--green-dark);color:var(--white);font-size:12px;display:flex;align-items:center;justify-content:center;height:38px;width:90px}

/* hero */
.hero{height:615px;background:linear-gradient(180deg,#6b5a3a 0%,#a27a3e 35%,#c48a3a 60%,#8a5a24 85%,#5c3d1a 100%)}
.hero-photo{position:absolute;inset:0}
.topbar{position:absolute;top:0;left:0;width:1200px;height:40px;background:var(--orange)}
.nav{position:absolute;top:0;right:145px;height:40px;display:flex;gap:30px;align-items:center;font-size:13px;color:var(--white)}
.nav .active{text-decoration:underline;text-underline-offset:4px}
.logo{position:absolute;left:110px;top:-29px;width:180px;height:180px;border-radius:50%;background:var(--white);display:flex;flex-direction:column;align-items:center;justify-content:flex-end;padding-bottom:38px;color:var(--orange);font-weight:700;font-size:15px;line-height:1.2;text-align:center}
.hero-text{left:145px;top:238px;width:480px;font-size:19.5px;font-weight:600;line-height:32px;color:#222}
.arrow{position:absolute;width:30px;height:30px}
.scroll-down{position:absolute;left:545px;top:575px;width:110px;height:55px;background:var(--white);border-radius:55px 55px 0 0}

/* welcome */
.welcome{height:538px}
.welcome h1{position:absolute;left:145px;top:100px;font-size:50px;font-weight:700;color:var(--green);line-height:1}
.welcome h2{position:absolute;left:145px;top:164px;font-size:30px;font-weight:400;color:var(--green);line-height:1}
.rule{position:absolute;height:4px;background:var(--orange)}
.welcome p{position:absolute;left:145px;top:252px;width:405px;font-size:12px;line-height:22.5px;color:var(--muted)}
.portrait{position:absolute;left:675px;top:80px;width:378px;height:378px;border-radius:50%;background:radial-gradient(circle at 50% 45%,#8c8a80 0%,#5d6a48 45%,#3d5a26 75%,#2d4219 100%)}

/* vision */
.vision{height:441px;background:linear-gradient(180deg,#3b362f,#4a4238 50%,#3a342c);color:var(--white);text-align:center}
.vision h2{position:absolute;left:0;width:1200px;top:143px;font-size:31px;font-weight:400}
.vision p{position:absolute;left:145px;width:910px;top:208px;font-size:19.5px;line-height:32px}

/* featured */
.featured{height:661px;background:var(--grey-bg)}
.section-title{position:absolute;left:0;width:1200px;text-align:center;font-size:33px;color:var(--green);font-weight:400}
.col-label{position:absolute;font-size:23px;color:#222}
.view-all{position:absolute;font-size:11.5px;color:var(--orange)}
.card{position:absolute;background:var(--white);box-shadow:0 1px 3px rgba(0,0,0,.12)}
.badge{position:absolute;color:var(--white);font-size:11px;display:flex;align-items:center;justify-content:center}
.badge.green{background:var(--green-dark)}
.badge.orange{background:var(--orange)}
.card h3{position:absolute;font-size:16px;font-weight:500;color:var(--green);line-height:21px}
.card p{position:absolute;font-size:10px;line-height:14.5px;color:var(--muted)}

/* news */
.news{height:523px}

/* twitter */
.tweets{height:245px;background:var(--sky);color:var(--white);text-align:center}
.tweets p{position:absolute;left:140px;width:920px;top:112px;font-size:17px;line-height:27px}
.tweets .date{position:absolute;left:0;width:1200px;top:178px;font-size:12px}

/* footer */
.site-footer{height:317px;background:var(--footer);color:#bbb}
.site-footer h4{position:absolute;top:54px;font-size:15.5px;font-weight:500;color:var(--orange)}
.links{position:absolute;top:90px;font-size:11px;line-height:24px;color:#ccc}
.contact-line{position:absolute;font-size:11px;color:#ccc;display:flex;align-items:center;gap:10px}
.foot-text{position:absolute;font-size:11px;line-height:16.5px;color:#ccc}
.email{position:absolute;left:828px;top:149px;width:227px;height:38px;background:#ddd;color:#444;font-size:11px;padding-left:16px;display:flex;align-items:center}
.divider{position:absolute;left:145px;width:910px;top:238px;height:1px;background:#555}
.copyright{position:absolute;left:0;width:1200px;top:268px;text-align:center;font-size:11px;color:#ccc}
</style>
</head>
<body>

<header class="hero">
  <div class="hero-photo" role="img" aria-label="Photo of a stag standing in golden grassland at sunrise"></div>
  <div class="topbar"></div>
  <nav class="nav">
    <span class="active">HOME</span><span>PEOPLE</span><span>PUBLICATIONS</span><span>PROJECTS</span><span>NEWS</span><span>CONTACT</span><span>COLLABORATORS</span>
  </nav>
  <div class="logo"><span>Creature Harmony</span><span>NexaForm lab</span></div>
  <p class="abs hero-text">We are researching the relationship between humans and wildlife, and seeking to explore ways for the two to coexist.</p>
  <div class="btn" style="left:145px;top:348px">Read More</div>
  <svg class="arrow" style="left:48px;top:312px" viewBox="0 0 30 30"><path d="M19 6 L10 15 L19 24" fill="none" stroke="#fff" stroke-width="3"/></svg>
  <svg class="arrow" style="left:1122px;top:312px" viewBox="0 0 30 30"><path d="M11 6 L20 15 L11 24" fill="none" stroke="#fff" stroke-width="3"/></svg>
  <div class="scroll-down"></div>
  <svg class="arrow" style="left:585px;top:582px" viewBox="0 0 30 30"><path d="M8 11 L15 18 L22 11" fill="none" stroke="#555" stroke-width="2.5"/></svg>
</header>

<section class="welcome">
  <h1>Welcome to</h1>
  <h2>Creature Harmony NexaForm lab</h2>
  <div class="rule" style="left:145px;top:225px;width:200px"></div>
  <p>Proin placerat dapibus gravida. In tristique tristique nulla eget hendrerit. Maecenas vel tortor accumsan quam varius imperdiet vel eget elit. Aenean facilisis tincidunt lectus, id dictum nisi luctus eget. Vivamus efficitur ex condimentum, malesuada eros eget, feugiat nibh. Sed tellus ex, imperdiet eget gravida sit amet.</p>
  <div class="btn" style="left:145px;top:384px">Read More</div>
  <div class="portrait" role="img" aria-label="Round photo of a raccoon standing up in green foliage"></div>
</section>

<section class="vision" role="img" aria-label="Dark background photo of a pride of lions walking on a track">
  <h2>Vision &nbsp;/&nbsp; Mission</h2>
  <div class="rule" style="left:470px;top:185px;width:95px"></div>
  <p>Phasellus nisl est, condimentum vitae faucibus in, sollicitudin vel metus. Nunc sit amet consequat risus. Curabitur ac elit leo. In eleifend dui tellus, in scelerisque elit porttitor et. Integer eu massa lacinia, lacinia nulla non, volutpat purus.</p>
</section>

<section class="featured">
  <h2 class="section-title" style="top:68px">Etiam mattis augue vehicula odio posuere</h2>
  <div class="rule" style="left:500px;top:134px;width:200px"></div>

  <div class="col-label" style="left:142px;top:175px">Researches</div>
  <div class="view-all" style="left:524px;top:183px">VIEW ALL</div>
  <div class="col-label" style="left:621px;top:175px">Resources</div>
  <div class="view-all" style="left:1002px;top:183px">VIEW ALL</div>

  <article class="card" style="left:145px;top:213px;width:433px;height:368px">
    <div class="abs" style="left:0;top:0;width:433px;height:192px;background:linear-gradient(180deg,#e89a3a,#d0701c 60%,#8a4a14)" role="img" aria-label="Photo of a leaping antelope silhouetted at sunset"></div>
    <div class="badge green" style="left:16px;top:212px;width:103px;height:29px">2 January, 2019</div>
    <h3 style="left:16px;top:256px;width:400px">Aliquam erat volutpat. Quisque aliquet ex nec est vestibulum pulvinar.</h3>
    <p style="left:16px;top:308px;width:400px">Vivamus eleifend vitae nulla vel malesuada. In ac malesuada lacus, et consectetur ante. Fusce vitae lectus sit amet mi pulvinar maximus. Aenean placerat, nibh vel accumsan aliquet, magna nibh accumsan nibh.</p>
  </article>

  <article class="card" style="left:621px;top:213px;width:434px;height:170px">
    <div class="abs" style="left:0;top:0;width:160px;height:170px;background:linear-gradient(160deg,#9aa0a4,#6a6e70 50%,#3a3a3a)" role="img" aria-label="Photo of a small finch perched on seed pods"></div>
    <div class="badge green" style="left:178px;top:29px;width:103px;height:29px">2 January, 2019</div>
    <h3 style="left:178px;top:76px;width:240px">Vestibulum ante ipsum primis in faucibus orci luctus et ultrices posuere</h3>
  </article>

  <article class="card" style="left:621px;top:414px;width:434px;height:170px">
    <div class="abs" style="left:0;top:0;width:160px;height:170px;background:linear-gradient(160deg,#5a8a2a,#c02a2a 55%,#7a1a14)" role="img" aria-label="Photo of two red-eyed tree frogs on a red flower"></div>
    <div class="badge green" style="left:178px;top:29px;width:103px;height:29px">2 January, 2019</div>
    <h3 style="left:178px;top:76px;width:240px">Phasellus nisl est, condimentum vitae faucibus in, sollicitudin vel metus</h3>
  </article>
</section>

<section class="news">
  <h2 class="section-title" style="top:80px">News &amp; Events</h2>
  <div class="rule" style="left:500px;top:143px;width:200px"></div>

  <article class="card" style="left:145px;top:180px;width:216px;height:218px;background:#ececec;box-shadow:none">
    <div class="badge orange" style="left:0;top:0;width:111px;height:36px">2 January, 2019</div>
    <h3 style="left:14px;top:58px;width:195px">Sed libero felis, vestibulum dolor eget, lacinia aliquet neque.</h3>
    <p style="left:14px;top:136px;width:190px">Fusce eget neque elit. Sed augue orci, elementum in magna congue, tincidunt vulputate erat.</p>
  </article>
  <article class="card" style="left:376px;top:180px;width:216px;height:218px;background:#ececec;box-shadow:none">
    <div class="badge orange" style="left:0;top:0;width:111px;height:36px">2 January, 2019</div>
    <h3 style="left:14px;top:58px;width:195px">Curabitur venenatis lacinia ornare. Cras sollicitudin cursus.</h3>
    <p style="left:14px;top:136px;width:190px">Fusce eget neque elit. Sed augue orci, elementum in magna congue, tincidunt vulputate erat.</p>
  </article>
  <article class="card" style="left:608px;top:180px;width:216px;height:218px;background:#ececec;box-shadow:none">
    <div class="badge orange" style="left:0;top:0;width:111px;height:36px">2 January, 2019</div>
    <h3 style="left:14px;top:58px;width:195px">Vivamus eleifend vitae nulla vel malesuada. In malesuada lacus.</h3>
    <p style="left:14px;top:136px;width:190px">Fusce eget neque elit. Sed augue orci, elementum in magna congue, tincidunt vulputate erat.</p>
  </article>
  <article class="card" style="left:839px;top:180px;width:216px;height:218px;background:#ececec;box-shadow:none">
    <div class="badge orange" style="left:0;top:0;width:111px;height:36px">2 January, 2019</div>
    <h3 style="left:14px;top:58px;width:195px">Aenean placerat, nibh vel accumsan aliquet, magna nibh.</h3>
    <p style="left:14px;top:136px;width:190px">Fusce eget neque elit. Sed augue orci, elementum in magna congue, tincidunt vulputate erat.</p>
  </article>

  <div class="view-all" style="left:573px;top:432px">VIEW ALL</div>
</section>

<section class="tweets">
  <div class="abs" style="left:587px;top:60px;width:26px;height:26px;border-radius:50%;background:var(--white)"></div>
  <svg class="arrow" style="left:48px;top:88px" viewBox="0 0 30 30"><path d="M19 6 L10 15 L19 24" fill="none" stroke="#fff" stroke-width="3"/></svg>
  <svg class="arrow" style="left:1122px;top:88px" viewBox="0 0 30 30"><path d="M11 6 L20 15 L11 24" fill="none" stroke="#fff" stroke-width="3"/></svg>
  <p>Phasellus nisl est, condimentum vitae faucibus in, sollicitudin vel metus. Nunc sit amet consequat risus. Curabitur ac elit leo. In eleifend dui tellus, in scelerisque elit porttitor et. Integer eu massa lacinia</p>
  <div class="date">2 January, 2019</div>
</section>

<footer class="site-footer">
  <h4 style="left:145px">Links</h4>
  <div class="links" style="left:145px">Home<br>People<br>Publications<br>Projects</div>
  <div class="links" style="left:225px">News<br>Contact<br>Collaborators</div>

  <h4 style="left:370px">Contact us</h4>
  <div class="contact-line" style="left:370px;top:88px;width:200px;align-items:flex-start">
    <svg width="10" height="13" viewBox="0 0 10 13"><path d="M5 0a5 5 0 0 1 5 5c0 3-5 8-5 8S0 8 0 5a5 5 0 0 1 5-5z" fill="#ccc"/><circle cx="5" cy="5" r="2" fill="#2b2b2b"/></svg>
    <span style="line-height:16px">24 Building name, Street name,<br>City Zipcode</span>
  </div>
  <div class="contact-line" style="left:370px;top:132px">
    <svg width="10" height="10" viewBox="0 0 10 10"><path d="M2 0l2 2.5-1.2 1.2a6 6 0 0 0 3.5 3.5L7.5 6 10 8 8.5 10C4 10 0 6 0 1.5z" fill="#ccc"/></svg>
    <span>456 870 3192</span>
  </div>
  <div class="contact-line" style="left:370px;top:157px">
    <svg width="11" height="8" viewBox="0 0 11 8"><rect width="11" height="8" fill="#ccc"/><path d="M0 0l5.5 4.5L11 0" fill="none" stroke="#2b2b2b" stroke-width="1"/></svg>
    <span>info@nexaformlab.org</span>
  </div>

  <h4 style="left:619px">Get In Touch</h4>
  <p class="foot-text" style="left:619px;top:90px;width:160px">Nulla ut neque mattis, ornare ipsum pellentesque, volutpat purus</p>
  <div class="abs" style="left:619px;top:156px;width:14px;height:14px;border-radius:50%;background:#ccc"></div>
  <div class="abs" style="left:651px;top:156px;width:14px;height:14px;border-radius:50%;background:#ccc"></div>

  <h4 style="left:828px">Join Our Newsletter</h4>
  <p class="foot-text" style="left:828px;top:90px;width:230px">To receive special offers, training materials and the latest information on essential and natural self-care.</p>
  <div class="email">Email Address
    <svg class="abs" style="right:12px;top:12px" width="18" height="13" viewBox="0 0 18 13"><rect width="18" height="13" fill="#444"/><path d="M0 0l9 7 9-7" fill="none" stroke="#ddd" stroke-width="1.5"/></svg>
  </div>

  <div class="divider"></div>
  <div class="copyright">Copyright &copy; 2019 Creature Harmony NexaForm lab. &nbsp;All rights reserved.</div>
</footer>

</body>
</html>
```